Lucky Harbour Fun Casino Entertainment

Looking to update my business card and make it look more modern, stand out and eye catching.
We are are fun casino business in Australia (primarily Sydney). Blackjack and Roulette are our most popular games although we have pretty much every game available for hire that you would find in a real casino. The final design would need to be sleek and appeal to the more upmarket corporate sector.
We mainly cater for Corporate Events, Private Parties, Fundraising Events, Team Building, Poker Tournaments
I think I'd prefer the colour Black.

Target Market(s)

High-end Corporate

Industry/Entity Type

Events

Contact Information for Business Card

Rob Kendall
Director
1300 482 617
0433 728 591
info@luckyharbour.com.au
www.luckyharbour.com.au
Facebook & Instagram @luckyharbourevents (proper social icons preferred)

Colors
000000
0255a3

Requirements
Must have
• Front side:
• Logo
• Contact details
• 'Australia's #1 Fun Casino Specialists'
• Back:
• Logo
Nice to have
• Back:
• Corporate Events
• Private Parties
• Poker Tournaments
• Fundraising
• Props & Theming
• Photo Booth
• Horse Racing Events
• The Vegas Sign attached, maybe on the back of the card in the background...?

```html
<!DOCTYPE html>
<html lang="en">
<head>
<meta charset="utf-8">
<title>Lucky Harbour Fun Casino Entertainment – Business Card</title>
<link rel="stylesheet" href="https://fonts.googleapis.com/css2?family=Montserrat:wght@400;500;700&family=Questrial&display=swap">
<style>
  :root {
    --stage: #141517;
    --card: #232528;
    --card-edge: #1b1c1f;
    --band: #1e9be0;
    --band-light: #4cb8f0;
    --band-ink: #0f2a3d;
    --gold: #f5a623;
    --gold-line: #b8902a;
    --blue-text: #1e9be0;
    --chip-blue: #2a57c8;
    --ink: #e8eaec;
  }
  * { margin: 0; padding: 0; box-sizing: border-box; }
  html, body { width: 1200px; height: 800px; overflow: hidden; background: var(--stage); }
  .stage { position: relative; width: 1200px; height: 800px; }

  .card {
    position: absolute;
    width: 620px; height: 354px;
    border-radius: 18px;
    background: radial-gradient(circle at 30% 30%, #2a2c30 0%, var(--card) 55%, var(--card-edge) 100%);
    box-shadow: 0 12px 30px rgba(0,0,0,.55);
    overflow: hidden;
    font-family: "Questrial", "Century Gothic", sans-serif;
    color: var(--ink);
  }
  .card--front { left: 60px; top: 36px; }
  .card--back { left: 520px; top: 418px; }

  .band {
    position: absolute; left: 0; right: 0; bottom: 44px; height: 44px;
    background: linear-gradient(180deg, var(--band-light) 0%, var(--band) 35%, var(--band) 100%);
    display: flex; align-items: center; justify-content: center;
    font-family: "Montserrat", sans-serif; font-weight: 700;
    font-size: 19px; letter-spacing: 3px; color: var(--band-ink);
  }

  .brand {
    position: absolute; left: 48px; top: 96px;
    display: flex; align-items: center; gap: 14px;
  }
  .brand__dot { width: 22px; height: 22px; border-radius: 50%; background: var(--gold); flex: none; }
  .brand__name {
    font-family: "Montserrat", sans-serif; font-weight: 700;
    font-size: 30px; color: var(--gold); letter-spacing: 1px; line-height: 1.05;
  }

  .divider {
    position: absolute; top: 56px; width: 1px; height: 130px;
    background: linear-gradient(180deg, transparent, var(--gold-line), transparent);
    transform: rotate(28deg);
  }
  .card--front .divider { left: 318px; }
  .card--back .divider { left: 300px; top: 70px; }

  .contact { position: absolute; left: 350px; top: 34px; }
  .contact__name {
    font-family: "Montserrat", sans-serif; font-weight: 500;
    font-size: 21px; color: var(--gold); letter-spacing: .5px;
  }
  .contact__role { font-size: 15px; color: var(--blue-text); margin-bottom: 10px; }
  .contact__list { list-style: none; }
  .contact__item { display: flex; align-items: center; gap: 9px; font-size: 14.5px; line-height: 22px; }
  .contact__icon { width: 16px; height: 16px; flex: none; }
  .contact__web .accent { color: var(--blue-text); }
  .contact__social { margin-top: 6px; }
  .social-dot { width: 15px; height: 15px; border-radius: 50%; background: var(--blue-text); flex: none; }

  .services { position: absolute; left: 345px; top: 40px; list-style: none; }
  .services__item { display: flex; align-items: center; gap: 12px; font-size: 16px; line-height: 25px; }
  .chip { width: 15px; height: 15px; flex: none; }
</style>
</head>
<body>
<main class="stage">

  <section class="card card--front" aria-label="Business card front">
    <div class="brand">
      <span class="brand__dot"></span>
      <span class="brand__name">LUCKY<br>HARBOUR</span>
    </div>
    <div class="divider"></div>
    <div class="contact">
      <p class="contact__name">ROB KENDALL</p>
      <p class="contact__role">Director</p>
      <ul class="contact__list">
        <li class="contact__item">
          <svg class="contact__icon" viewBox="0 0 16 16"><circle cx="8" cy="8" r="8" fill="#f5a623"/><path d="M5 4.5l1.6-.3.8 2-1 .8a5 5 0 0 0 2.6 2.6l.8-1 2 .8-.3 1.6c-3.6.3-6.8-2.9-6.5-6.5z" fill="#232528"/></svg>
          1300 482 617
        </li>
        <li class="contact__item">
          <svg class="contact__icon" viewBox="0 0 16 16"><circle cx="8" cy="8" r="8" fill="#f5a623"/><rect x="5.5" y="3.5" width="5" height="9" rx="1" fill="none" stroke="#232528" stroke-width="1.3"/></svg>
          0433 728 591
        </li>
        <li class="contact__item">
          <svg class="contact__icon" viewBox="0 0 16 16"><circle cx="8" cy="8" r="8" fill="#f5a623"/><rect x="4" y="5" width="8" height="6" fill="none" stroke="#232528" stroke-width="1.2"/><path d="M4 5l4 3.2L12 5" fill="none" stroke="#232528" stroke-width="1.2"/></svg>
          info@luckyharbour.com.au
        </li>
        <li class="contact__item contact__web">
          <svg class="contact__icon" viewBox="0 0 16 16"><circle cx="8" cy="8" r="8" fill="#f5a623"/><circle cx="8" cy="8" r="4" fill="none" stroke="#232528" stroke-width="1.2"/><path d="M4 8h8M8 4c-2 2.5-2 5.5 0 8M8 4c2 2.5 2 5.5 0 8" fill="none" stroke="#232528" stroke-width="1"/></svg>
          <span>www.<span class="accent">luckyharbour</span>.com.au</span>
        </li>
        <li class="contact__item contact__social">
          <span class="social-dot"></span><span class="social-dot"></span>
          @luckyharbourevents
        </li>
      </ul>
    </div>
    <div class="band">Australia's #1 Fun Casino Specialists</div>
  </section>

  <section class="card card--back" aria-label="Business card back">
    <div class="brand">
      <span class="brand__dot"></span>
      <span class="brand__name">LUCKY<br>HARBOUR</span>
    </div>
    <div class="divider"></div>
    <ul class="services">
      <li class="services__item"><svg class="chip" viewBox="0 0 16 16"><circle cx="8" cy="8" r="7.5" fill="#2a57c8"/><circle cx="8" cy="8" r="4.5" fill="none" stroke="#fff" stroke-width="1.4" stroke-dasharray="2 2"/></svg>Corporate Events</li>
      <li class="services__item"><svg class="chip" viewBox="0 0 16 16"><circle cx="8" cy="8" r="7.5" fill="#2a57c8"/><circle cx="8" cy="8" r="4.5" fill="none" stroke="#fff" stroke-width="1.4" stroke-dasharray="2 2"/></svg>Private Parties</li>
      <li class="services__item"><svg class="chip" viewBox="0 0 16 16"><circle cx="8" cy="8" r="7.5" fill="#2a57c8"/><circle cx="8" cy="8" r="4.5" fill="none" stroke="#fff" stroke-width="1.4" stroke-dasharray="2 2"/></svg>Poker Tournaments</li>
      <li class="services__item"><svg class="chip" viewBox="0 0 16 16"><circle cx="8" cy="8" r="7.5" fill="#2a57c8"/><circle cx="8" cy="8" r="4.5" fill="none" stroke="#fff" stroke-width="1.4" stroke-dasharray="2 2"/></svg>Fundraising</li>
      <li class="services__item"><svg class="chip" viewBox="0 0 16 16"><circle cx="8" cy="8" r="7.5" fill="#2a57c8"/><circle cx="8" cy="8" r="4.5" fill="none" stroke="#fff" stroke-width="1.4" stroke-dasharray="2 2"/></svg>Props &amp; Theming</li>
      <li class="services__item"><svg class="chip" viewBox="0 0 16 16"><circle cx="8" cy="8" r="7.5" fill="#2a57c8"/><circle cx="8" cy="8" r="4.5" fill="none" stroke="#fff" stroke-width="1.4" stroke-dasharray="2 2"/></svg>Photo Booth</li>
      <li class="services__item"><svg class="chip" viewBox="0 0 16 16"><circle cx="8" cy="8" r="7.5" fill="#2a57c8"/><circle cx="8" cy="8" r="4.5" fill="none" stroke="#fff" stroke-width="1.4" stroke-dasharray="2 2"/></svg>Horse Racing Events</li>
    </ul>
    <div class="band">www.luckyharbour.com.au</div>
  </section>

</main>
</body>
</html>
```